UX Design for Analytics Web Application

http://velqoranthe.com/
We are tech & consulting company with analytics products (web applications), located at Rio de Janeiro, Brazil.

We are searching a partner do develop UX for our products, i.e, aesthetics, usability, HTML/CSS.

Currently we have a product suite and the goal is to make a pilot re-design project with one of our products.

The product of interest is interactive webapp that aims at data analysis, significantly different from blogs, e-commerce or landing pages.

We do have a software development team but we lack an UX & HTML expert. Currently we use Bootstrap templates but the results are insatisfatory.

So, the project scope is, to develop the arts (UX, aesthetics, etc) along with the code/mockup (HTML/CSS) for one of our product (3 pages).

This is a pilot project and there's potential to rehire for our other products. Code quality is of importance.

More details and specification can be found in attached files.

Target Market(s)

Executives, managers & consultants

Industry/Entity Type

It Company

Coding

Coded - Design and coding required

Number of Pages Required

3 page

Font styles to use
Sans Serif

Requirements
Must have
• (see attached files, prefer the pptx version))
• -Responsive
Nice to have
• (see attached files, prefer the pptx version)
Should not have
• -Avoid Green, Red and Yellow colors. They have a meaning of good, bad and average in our products.

```html
<!DOCTYPE html>
<html lang="en">
<head>
<meta charset="utf-8">
<title>Velqor – Processes Dashboard</title>
<link href="https://fonts.googleapis.com/css2?family=Roboto:wght@300;400;500;700&display=swap" rel="stylesheet">
<style>
:root{
  --page-bg:#c3e8fb;
  --panel:#ffffff;
  --card:#f7f7f7;
  --line:#e3e3e3;
  --text:#3d3d3d;
  --muted:#555;
  --teal:#2ec1bd;
  --sky:#5acdf5;
  --link:#1a9fe0;
  --grey-ring:#e4e7ea;
  --footer:#252525;
  --icon:#5a5a5a;
}
*{box-sizing:border-box;margin:0;padding:0}
html,body{width:1200px;height:1126px;overflow:hidden}
body{font-family:"Roboto",sans-serif;color:var(--text);background:var(--page-bg);position:relative}

.site-header{position:absolute;left:0;top:0;width:1200px;height:93px;background:#fff;border-bottom:1px solid #d7e9f2}
.brand{position:absolute;left:100px;top:22px;display:flex;align-items:center;gap:8px;font-size:36px;font-weight:500;color:var(--icon);letter-spacing:.5px}
.brand-dot{width:34px;height:34px;border-radius:50%;border:3px solid var(--icon)}
.header-actions{position:absolute;right:96px;top:34px;display:flex;gap:20px}
.header-actions svg{width:22px;height:22px;fill:var(--icon)}

.panel{position:absolute;background:var(--panel);border:1px solid #d5e4ec}

.summary{left:19px;top:118px;width:461px;height:364px}
.summary h1{font-weight:400;font-size:26px;text-align:center;margin-top:26px;letter-spacing:.3px;transform:scaleX(.92)}
.donut{position:absolute;left:161px;top:80px;width:138px;height:138px}
.donut-label{position:absolute;left:161px;top:80px;width:138px;height:138px;display:flex;flex-direction:column;align-items:center;justify-content:center;font-size:14px;line-height:17px}
.stats{position:absolute;left:25px;top:236px;width:420px}
.stat{display:flex;align-items:center;height:31px}
.stat-label{width:213px;font-size:15.5px}
.stat-label.lead{font-size:21px;height:38px;display:flex;align-items:center}
.bar{width:170px;height:11px;border-radius:6px;background:#eaeaea;border:1px solid #ddd;overflow:hidden}
.bar span{display:block;height:100%;border-radius:6px}
.bar .teal{background:var(--teal);width:91%}
.bar .sky{background:var(--sky);width:46%}
.pct{margin-left:12px;font-size:13px;color:var(--teal)}

.feed{left:19px;top:502px;width:461px;height:410px}
.feed h2{font-weight:400;font-size:20px;padding:24px 25px 0;height:64px;border-bottom:1px solid var(--line)}
.feed-item{display:flex;gap:26px;padding:16px 25px 0;border-bottom:1px solid var(--line)}
.feed-item:last-child{border-bottom:none}
.feed-item .avatar{width:66px;height:66px;border-radius:50%;flex:none;background:radial-gradient(circle at 50% 40%,#c9a58a,#6c4a36)}
.feed-text{font-size:14.5px;line-height:21px}
.feed-text a{color:var(--link);text-decoration:none}
.feed-time{font-size:13px;margin-top:8px;color:var(--muted)}

.toolbar{position:absolute;left:495px;top:120px;display:flex;gap:6px}
.tool{height:41px;background:#f3f3f3;border:1px solid #dbe3e7;display:flex;align-items:center;justify-content:center;gap:10px;font-size:18px;color:var(--text)}
.tool svg{width:15px;height:15px;fill:var(--icon)}

.grid-panel{left:495px;top:173px;width:684px;height:739px}
.card{position:absolute;width:206px;height:207px;background:var(--card);border:1px solid #e2e2e2}
.card-photo{height:70px;position:relative;overflow:hidden}
.card-photo .tick{position:absolute;right:0;top:0;width:0;height:0;border-top:44px solid var(--teal);border-left:44px solid transparent}
.card-photo svg{position:absolute;right:4px;top:5px;width:14px;height:14px}
.card-head{display:flex;align-items:center;padding:16px 10px 0 13px;gap:6px}
.mini-avatar{width:30px;height:30px;border-radius:50%;background:radial-gradient(circle at 50% 40%,#d8c5b7,#7c8894);flex:none}
.card-title{font-size:15px;line-height:17px;width:100px}
.mini-donut{margin-left:auto;width:44px;height:44px}
.card-body{font-size:12.5px;line-height:20px;padding:16px 20px 0;color:var(--muted)}

.site-footer{position:absolute;left:0;top:947px;width:1200px;height:179px;background:var(--footer);color:#fff;text-align:center}
.social{display:flex;justify-content:center;gap:10px;margin-top:39px}
.social span{width:20px;height:20px;border-radius:3px;background:#fff}
.footer-brand{display:flex;justify-content:center;align-items:center;gap:8px;font-size:40px;font-weight:500;margin-top:14px}
.footer-brand .brand-dot{border-color:#fff;width:40px;height:40px}
.copyright{font-size:11.5px;margin-top:10px}
</style>
</head>
<body>

<header class="site-header">
  <div class="brand"><span class="brand-dot"></span>Velqor</div>
  <nav class="header-actions">
    <svg viewBox="0 0 24 24"><path d="M12 2a2 2 0 0 1 2 2v1a6 6 0 0 1 4 6v5l2 2v1H4v-1l2-2v-5a6 6 0 0 1 4-6V4a2 2 0 0 1 2-2zm-2 19h4a2 2 0 0 1-4 0z"/></svg>
    <svg viewBox="0 0 24 24"><circle cx="12" cy="7" r="5"/><path d="M2 22c0-6 4-8 10-8s10 2 10 8z"/></svg>
    <svg viewBox="0 0 24 24"><path d="M10 1h4l1 3 3-1 3 3-1 3 3 1v4l-3 1 1 3-3 3-3-1-1 3h-4l-1-3-3 1-3-3 1-3-3-1v-4l3-1-1-3 3-3 3 1zm2 7a4 4 0 1 0 0 8 4 4 0 0 0 0-8z"/></svg>
  </nav>
</header>

<section class="panel summary">
  <h1>14 ACTIVE PROCESSES</h1>
  <svg class="donut" viewBox="0 0 138 138">
    <g transform="rotate(-90 69 69)" fill="none" stroke-width="28">
      <circle cx="69" cy="69" r="55" stroke="var(--grey-ring)"/>
      <circle cx="69" cy="69" r="55" stroke="var(--sky)" stroke-dasharray="318 346" />
      <circle cx="69" cy="69" r="55" stroke="var(--teal)" stroke-dasharray="249 346"/>
    </g>
    <g stroke="#fff" stroke-width="3"><line x1="69" y1="0" x2="69" y2="30"/></g>
  </svg>
  <div class="donut-label"><span>72%</span><span>concluded</span></div>
  <div class="stats">
    <div class="stat"><div class="stat-label lead">31 millions expent</div><div class="bar"><span class="teal"></span></div></div>
    <div class="stat"><div class="stat-label">with 2 millions of gap</div><div class="bar"><span class="sky"></span></div><span class="pct">6%</span></div>
    <div class="stat"><div class="stat-label">and 1.5 million negotiated</div><div class="bar"><span class="sky"></span></div><span class="pct">5%</span></div>
  </div>
</section>

<section class="panel feed">
  <h2>ACTIVITY FEED</h2>
  <article class="feed-item" style="height:124px">
    <div class="avatar" role="img" aria-label="Profile photo of Lucas Brenner"></div>
    <div><p class="feed-text"><a href="#">Lucas Brenner</a> upload new data with 23823<br>rows to the <a href="#">XPTO Process</a> and<br>he is happy now –</p><p class="feed-time">3 days ago</p></div>
  </article>
  <article class="feed-item" style="height:112px">
    <div class="avatar" role="img" aria-label="Profile photo of Maya Orlen"></div>
    <div><p class="feed-text"><a href="#">Maya Orlen</a> started the<br><a href="#">ABC process</a> –</p><p class="feed-time" style="margin-top:12px">3 days ago</p></div>
  </article>
  <article class="feed-item">
    <div class="avatar" role="img" aria-label="Profile photo of Tomas Varela"></div>
    <div><p class="feed-text"><a href="#">Tomas Varela</a> is making a new content layout<br>specification –</p><p class="feed-time">3 days ago</p></div>
  </article>
</section>

<div class="toolbar">
  <div class="tool" style="width:131px"><svg viewBox="0 0 16 16"><path d="M6.5 1a5.5 5.5 0 0 1 4.4 8.8l4 4-1.4 1.4-4-4A5.5 5.5 0 1 1 6.5 1zm0 2.2a3.3 3.3 0 1 0 0 6.6 3.3 3.3 0 0 0 0-6.6z"/></svg>Search</div>
  <div class="tool" style="width:132px"><svg viewBox="0 0 16 16"><path d="M3 1h2v10h2l-3 4-3-4h2zM8 2h7v2H8zm0 4h5v2H8zm0 4h3v2H8z"/></svg>Sort By</div>
  <div class="tool" style="width:131px"><svg viewBox="0 0 16 16"><path d="M1 2h14L10 8v6l-4-2V8z"/></svg>Filter By</div>
  <div class="tool" style="width:159px"><svg viewBox="0 0 16 16"><path d="M8 1a7 7 0 1 1 0 14A7 7 0 0 1 8 1zm-1 3v3H4v2h3v3h2V9h3V7H9V4z"/></svg>Add Process</div>
</div>

<section class="panel grid-panel">
  <!-- row 1 -->
  <article class="card" style="left:19px;top:25px"><div class="card-photo" role="img" aria-label="City waterfront at sunset" style="background:linear-gradient(#c28a73,#8a6f8a 50%,#b06a4a)"><span class="tick"></span><svg viewBox="0 0 14 14"><path d="M1 7l4 4 8-8" stroke="#fff" stroke-width="2.5" fill="none"/></svg></div>
    <div class="card-head"><div class="mini-avatar" role="img" aria-label="Owner profile photo"></div><div class="card-title">14 million in expenses</div><svg class="mini-donut" viewBox="0 0 44 44"><circle cx="22" cy="22" r="17" fill="none" stroke="var(--grey-ring)" stroke-width="7"/><circle cx="22" cy="22" r="17" fill="none" stroke="var(--sky)" stroke-width="7" stroke-dasharray="95 107" transform="rotate(-90 22 22)"/><circle cx="22" cy="22" r="17" fill="none" stroke="var(--teal)" stroke-width="7" stroke-dasharray="70 107" transform="rotate(-90 22 22)"/><text x="22" y="27" text-anchor="middle" font-size="13" fill="var(--sky)" font-family="Roboto,sans-serif">$20</text></svg></div>
    <p class="card-body">Some short free text with links and 13,432 numbers</p></article>
  <article class="card" style="left:240px;top:25px"><div class="card-photo" role="img" aria-label="Downtown skyscrapers" style="background:linear-gradient(#b9a892,#6e5f50)"><span class="tick"></span><svg viewBox="0 0 14 14"><path d="M1 7l4 4 8-8" stroke="#fff" stroke-width="2.5" fill="none"/></svg></div>
    <div class="card-head"><div class="mini-avatar" role="img" aria-label="Owner profile photo"></div><div class="card-title">14 million in expenses</div><svg class="mini-donut" viewBox="0 0 44 44"><circle cx="22" cy="22" r="17" fill="none" stroke="var(--grey-ring)" stroke-width="7"/><circle cx="22" cy="22" r="17" fill="none" stroke="var(--sky)" stroke-width="7" stroke-dasharray="95 107" transform="rotate(-90 22 22)"/><circle cx="22" cy="22" r="17" fill="none" stroke="var(--teal)" stroke-width="7" stroke-dasharray="70 107" transform="rotate(-90 22 22)"/><text x="22" y="27" text-anchor="middle" font-size="13" fill="var(--sky)" font-family="Roboto,sans-serif">$20</text></svg></div>
    <p class="card-body">Some short free text with links and 13,432 numbers</p></article>
  <article class="card" style="left:460px;top:25px"><div class="card-photo" role="img" aria-label="City towers at dusk" style="background:linear-gradient(#3d5d8a,#c9862f)"><span class="tick"></span><svg viewBox="0 0 14 14"><path d="M1 7l4 4 8-8" stroke="#fff" stroke-width="2.5" fill="none"/></svg></div>
    <div class="card-head"><div class="mini-avatar" role="img" aria-label="Owner profile photo"></div><div class="card-title">14 million in expenses</div><svg class="mini-donut" viewBox="0 0 44 44"><circle cx="22" cy="22" r="17" fill="none" stroke="var(--grey-ring)" stroke-width="7"/><circle cx="22" cy="22" r="17" fill="none" stroke="var(--sky)" stroke-width="7" stroke-dasharray="95 107" transform="rotate(-90 22 22)"/><circle cx="22" cy="22" r="17" fill="none" stroke="var(--teal)" stroke-width="7" stroke-dasharray="70 107" transform="rotate(-90 22 22)"/><text x="22" y="27" text-anchor="middle" font-size="13" fill="var(--sky)" font-family="Roboto,sans-serif">$20</text></svg></div>
    <p class="card-body">Some short free text with links and 13,432 numbers</p></article>
  <!-- row 2 -->
  <article class="card" style="left:19px;top:259px"><div class="card-photo" role="img" aria-label="Skyline at night" style="background:linear-gradient(#4a5a86,#1d2436)"><span class="tick"></span><svg viewBox="0 0 14 14"><path d="M1 7l4 4 8-8" stroke="#fff" stroke-width="2.5" fill="none"/></svg></div>
    <div class="card-head"><div class="mini-avatar" role="img" aria-label="Owner profile photo"></div><div class="card-title">14 million in expenses</div><svg class="mini-donut" viewBox="0 0 44 44"><circle cx="22" cy="22" r="17" fill="none" stroke="var(--grey-ring)" stroke-width="7"/><circle cx="22" cy="22" r="17" fill="none" stroke="var(--sky)" stroke-width="7" stroke-dasharray="95 107" transform="rotate(-90 22 22)"/><circle cx="22" cy="22" r="17" fill="none" stroke="var(--teal)" stroke-width="7" stroke-dasharray="70 107" transform="rotate(-90 22 22)"/><text x="22" y="27" text-anchor="middle" font-size="13" fill="var(--sky)" font-family="Roboto,sans-serif">$20</text></svg></div>
    <p class="card-body">Some short free text with links and 13,432 numbers</p></article>
  <article class="card" style="left:240px;top:259px"><div class="card-photo" role="img" aria-label="Crowded street in warm light" style="background:linear-gradient(100deg,#3e4a5a,#c9a36a)"><span class="tick"></span><svg viewBox="0 0 14 14"><path d="M1 7l4 4 8-8" stroke="#fff" stroke-width="2.5" fill="none"/></svg></div>
    <div class="card-head"><div class="mini-avatar" role="img" aria-label="Owner profile photo"></div><div class="card-title">14 million in expenses</div><svg class="mini-donut" viewBox="0 0 44 44"><circle cx="22" cy="22" r="17" fill="none" stroke="var(--grey-ring)" stroke-width="7"/><circle cx="22" cy="22" r="17" fill="none" stroke="var(--sky)" stroke-width="7" stroke-dasharray="95 107" transform="rotate(-90 22 22)"/><circle cx="22" cy="22" r="17" fill="none" stroke="var(--teal)" stroke-width="7" stroke-dasharray="70 107" transform="rotate(-90 22 22)"/><text x="22" y="27" text-anchor="middle" font-size="13" fill="var(--sky)" font-family="Roboto,sans-serif">$20</text></svg></div>
    <p class="card-body">Some short free text with links and 13,432 numbers</p></article>
  <article class="card" style="left:460px;top:259px"><div class="card-photo" role="img" aria-label="Illuminated towers at twilight" style="background:linear-gradient(#6a4f7e,#2e2f4a)"><span class="tick"></span><svg viewBox="0 0 14 14"><path d="M1 7l4 4 8-8" stroke="#fff" stroke-width="2.5" fill="none"/></svg></div>
    <div class="card-head"><div class="mini-avatar" role="img" aria-label="Owner profile photo"></div><div class="card-title">14 million in expenses</div><svg class="mini-donut" viewBox="0 0 44 44"><circle cx="22" cy="22" r="17" fill="none" stroke="var(--grey-ring)" stroke-width="7"/><circle cx="22" cy="22" r="17" fill="none" stroke="var(--sky)" stroke-width="7" stroke-dasharray="95 107" transform="rotate(-90 22 22)"/><circle cx="22" cy="22" r="17" fill="none" stroke="var(--teal)" stroke-width="7" stroke-dasharray="70 107" transform="rotate(-90 22 22)"/><text x="22" y="27" text-anchor="middle" font-size="13" fill="var(--sky)" font-family="Roboto,sans-serif">$20</text></svg></div>
    <p class="card-body">Some short free text with links and 13,432 numbers</p></article>
  <!-- row 3 -->
  <article class="card" style="left:19px;top:499px"><div class="card-photo" role="img" aria-label="Harbour city at night" style="background:linear-gradient(#5a6c94,#3a3344)"><span class="tick"></span><svg viewBox="0 0 14 14"><path d="M1 7l4 4 8-8" stroke="#fff" stroke-width="2.5" fill="none"/></svg></div>
    <div class="card-head"><div class="mini-avatar" role="img" aria-label="Owner profile photo"></div><div class="card-title">14 million in expenses</div><svg class="mini-donut" viewBox="0 0 44 44"><circle cx="22" cy="22" r="17" fill="none" stroke="var(--grey-ring)" stroke-width="7"/><circle cx="22" cy="22" r="17" fill="none" stroke="var(--sky)" stroke-width="7" stroke-dasharray="95 107" transform="rotate(-90 22 22)"/><circle cx="22" cy="22" r="17" fill="none" stroke="var(--teal)" stroke-width="7" stroke-dasharray="70 107" transform="rotate(-90 22 22)"/><text x="22" y="27" text-anchor="middle" font-size="13" fill="var(--sky)" font-family="Roboto,sans-serif">$20</text></svg></div>
    <p class="card-body">Some short free text with links and 13,432 numbers</p></article>
  <article class="card" style="left:240px;top:499px"><div class="card-photo" role="img" aria-label="Traveller by the seaside" style="background:linear-gradient(90deg,#c9b6a6,#8fb8d8)"><span class="tick"></span><svg viewBox="0 0 14 14"><path d="M1 7l4 4 8-8" stroke="#fff" stroke-width="2.5" fill="none"/></svg></div>
    <div class="card-head"><div class="mini-avatar" role="img" aria-label="Owner profile photo"></div><div class="card-title">14 million in expenses</div><svg class="mini-donut" viewBox="0 0 44 44"><circle cx="22" cy="22" r="17" fill="none" stroke="var(--grey-ring)" stroke-width="7"/><circle cx="22" cy="22" r="17" fill="none" stroke="var(--sky)" stroke-width="7" stroke-dasharray="95 107" transform="rotate(-90 22 22)"/><circle cx="22" cy="22" r="17" fill="none" stroke="var(--teal)" stroke-width="7" stroke-dasharray="70 107" transform="rotate(-90 22 22)"/><text x="22" y="27" text-anchor="middle" font-size="13" fill="var(--sky)" font-family="Roboto,sans-serif">$20</text></svg></div>
    <p class="card-body">Some short free text with links and 13,432 numbers</p></article>
  <article class="card" style="left:460px;top:499px"><div class="card-photo" role="img" aria-label="Marina at evening" style="background:linear-gradient(#3c4a55,#5f6b5c)"><span class="tick"></span><svg viewBox="0 0 14 14"><path d="M1 7l4 4 8-8" stroke="#fff" stroke-width="2.5" fill="none"/></svg></div>
    <div class="card-head"><div class="mini-avatar" role="img" aria-label="Owner profile photo"></div><div class="card-title">14 million in expenses</div><svg class="mini-donut" viewBox="0 0 44 44"><circle cx="22" cy="22" r="17" fill="none" stroke="var(--grey-ring)" stroke-width="7"/><circle cx="22" cy="22" r="17" fill="none" stroke="var(--sky)" stroke-width="7" stroke-dasharray="95 107" transform="rotate(-90 22 22)"/><circle cx="22" cy="22" r="17" fill="none" stroke="var(--teal)" stroke-width="7" stroke-dasharray="70 107" transform="rotate(-90 22 22)"/><text x="22" y="27" text-anchor="middle" font-size="13" fill="var(--sky)" font-family="Roboto,sans-serif">$20</text></svg></div>
    <p class="card-body">Some short free text with links and 13,432 numbers</p></article>
</section>

<footer class="site-footer">
  <div class="social" aria-label="Social links"><span></span><span></span><span></span><span></span><span></span></div>
  <div class="footer-brand"><span class="brand-dot"></span>Velqor</div>
  <p class="copyright">Copyright @ 2017 Velqor. All Rights Reserved.</p>
</footer>

</body>
</html>
```